FinTech company looking to revamp and expand client-facing interface for our financial models

Pellworth Engines currently has a very simple website that allows clients to interact with our financial models. We are looking to completely redesign the current site and add several extra pages to provide extra functionality. We want the design to have a modern, slick feel, that will work on both a desktop or a tablet. It should be straightforward for clients to move between different pages at any time, and clear from the layout how to interact with the more advanced features. We have included screenshots of existing pages in the attached design brief, as well as sketches of the functionality required by the new pages, but can't provide a direct link to the current site.
Target Market(s)
Professional investors that will be paying to access the interface
Industry/Entity Type
Finance
Number of Pages Required
4 page
Colors
Designer to choose colors to be used in the design.
Look and feel
Each slider illustrates characteristics of the customer's brand and the style your logo design should communicate.

```html
<!DOCTYPE html>
<html lang="en">
<head>
<meta charset="utf-8">
<title>QLENS – ETF Pairs</title>
<link rel="stylesheet" href="https://fonts.googleapis.com/css2?family=Open+Sans:wght@400;600;700&family=Roboto+Condensed:wght@400;500&display=swap">
<style>
:root{
  --frame:#e4e4e4;
  --white:#ffffff;
  --dark:#333333;
  --navy:#05336a;
  --grey-head:#666666;
  --band:#cccccc;
  --line:#e2e2e2;
  --row-alt:#f4f4f4;
  --ink:#111111;
  --tab-ink:#555555;
  --link:#1f4f9a;
}
*{box-sizing:border-box;margin:0;padding:0}
html,body{width:1200px;height:715px;overflow:hidden;background:var(--frame)}
.stage{width:1300px;height:775px;transform:scale(0.9231);transform-origin:0 0;position:relative;font-family:"Open Sans",sans-serif}
.app{position:absolute;left:15px;top:15px;width:1270px;height:745px;background:var(--white);overflow:hidden}
.topbar{position:absolute;left:0;top:0;width:1270px;height:60px;display:flex;background:var(--white);border-bottom:1px solid var(--line)}
.brand{width:180px;padding-left:58px;line-height:60px;font-weight:700;font-size:18px;color:var(--ink)}
.period{width:90px;text-align:center;line-height:60px;font-weight:700;font-size:14px;color:var(--ink);border-right:1px solid var(--line)}
.period.active{background:var(--dark);color:var(--white)}
.spacer{flex:1}
.nav-item{display:flex;align-items:center;justify-content:center;gap:8px;font-weight:700;font-size:13px;color:var(--ink);border-left:1px solid var(--line)}
.nav-item.active{background:var(--dark);color:var(--white)}
.nav-item svg{width:22px;height:22px}
.band{position:absolute;left:0;top:60px;width:1270px;height:95px;background:var(--band)}
.tab{position:absolute;bottom:0;width:155px;background:var(--white);border-radius:5px 5px 0 0;text-align:center;font-weight:600;font-size:13px;color:var(--tab-ink)}
.tab.short{height:35px;line-height:37px}
.tab.mid{height:45px;line-height:44px}
.tab.active{height:55px;line-height:56px;background:var(--navy);color:var(--white)}
.tab.faded{color:#c4c4c4}
.content{position:absolute;left:0;top:155px;width:1270px;height:590px;background:linear-gradient(180deg,#ececec 0%,#fbfbfb 45%,#fdfdfd 100%)}
.filters{position:absolute;left:57px;top:40px;display:flex;align-items:center;font-size:17px;color:var(--ink)}
.filters b{font-weight:700;margin-left:10px}
.filters input{width:180px;height:31px;margin-left:12px;border:1px solid #cfcfcf;border-radius:4px;padding-left:10px;font:17px "Open Sans",sans-serif;color:var(--ink);background:var(--white)}
.filters .gap{width:43px}
.export{position:absolute;right:55px;top:43px;display:flex;align-items:center;gap:8px;font-weight:600;font-size:17px;color:var(--link)}
.models{position:absolute;left:55px;top:110px;width:1160px;border-collapse:collapse;border-radius:7px;overflow:hidden;box-shadow:0 2px 8px rgba(0,0,0,.15);font-family:"Roboto Condensed",sans-serif;font-size:17px;color:var(--ink);background:var(--white);table-layout:fixed}
.models th{height:70px;color:var(--white);font-family:"Open Sans",sans-serif;font-weight:600;font-size:17px;background:var(--grey-head);border-right:1px solid #7a7a7a}
.models th.key{background:var(--navy);border-right:1px solid #1c4a80}
.models td{height:69px;padding-left:10px;border-right:1px solid var(--line);line-height:21px}
.models td.id{padding-left:22px}
.models tr:nth-child(even) td{background:var(--row-alt)}
.models td.num{text-align:left}
</style>
</head>
<body>
<div class="stage">
  <div class="app">
    <header class="topbar">
      <div class="brand">QLENS</div>
      <div class="period active">250D</div>
      <div class="period">83D</div>
      <div class="period">42D</div>
      <div class="spacer"></div>
      <div class="nav-item active" style="width:140px">
        <svg viewBox="0 0 24 24" fill="none" stroke="#fff" stroke-width="2"><path d="M3 11 12 3l9 8"/><path d="M5 10v10h5v-6h4v6h5V10"/></svg>MODELS</div>
      <div class="nav-item" style="width:178px">
        <svg viewBox="0 0 24 24" fill="#333"><circle cx="12" cy="12" r="3"/><circle cx="12" cy="3" r="1.5"/><circle cx="12" cy="21" r="1.5"/><circle cx="3" cy="12" r="1.5"/><circle cx="21" cy="12" r="1.5"/><circle cx="5.6" cy="5.6" r="1.5"/><circle cx="18.4" cy="18.4" r="1.5"/><circle cx="5.6" cy="18.4" r="1.5"/><circle cx="18.4" cy="5.6" r="1.5"/><circle cx="12" cy="7.5" r="1"/><circle cx="12" cy="16.5" r="1"/><circle cx="7.5" cy="12" r="1"/><circle cx="16.5" cy="12" r="1"/></svg>SENSITIVITIES</div>
      <div class="nav-item" style="width:168px;margin-right:29px">
        <svg viewBox="0 0 24 24" fill="none" stroke="#111" stroke-width="1.8"><path d="M12 2.5l2.9 6.2 6.6.7-5 4.5 1.4 6.6L12 17.2l-5.9 3.3 1.4-6.6-5-4.5 6.6-.7z"/></svg>FAVOURITES</div>
    </header>

    <nav class="band">
      <div class="tab short" style="left:55px">EQUITIES</div>
      <div class="tab short" style="left:215px">ETFS</div>
      <div class="tab mid" style="left:375px">PAIRS</div>
      <div class="tab active" style="left:535px">ETF PAIRS</div>
      <div class="tab mid" style="left:695px">FACTORS</div>
      <div class="tab short" style="left:855px">NEW TAB TITLE #1</div>
      <div class="tab short" style="left:1015px">NEW TAB TITLE #2</div>
      <div class="tab short faded" style="left:1175px;text-align:left;padding-left:18px">NEW TAB TITLE #3</div>
    </nav>

    <main class="content">
      <div class="filters">
        Quality <b>Threshold:</b><input value="-10">
        <span class="gap"></span>
        <b style="margin-left:0">Abs.</b>&nbsp;Stat <b>Threshold:</b><input value="-10">
      </div>
      <div class="export">
        <svg width="26" height="24" viewBox="0 0 26 24" fill="none" stroke="#1f4f9a" stroke-width="2.2"><path d="M10 5H4v15h15v-6"/><path d="M11 14c1-5 5-8 11-8"/><path d="M18 2l4 4-4 4"/></svg>Export
      </div>

      <table class="models">
        <colgroup>
          <col style="width:100px"><col style="width:110px"><col style="width:115px"><col style="width:115px">
          <col style="width:90px"><col style="width:90px"><col style="width:90px"><col style="width:90px">
          <col style="width:90px"><col style="width:90px"><col style="width:90px"><col style="width:90px">
        </colgroup>
        <thead>
          <tr>
            <th class="key">ID &#8964;</th><th class="key">Sector</th><th class="key">Time</th>
            <th>Quality</th><th>Stat 1</th><th>Stat 2</th><th>Stat 3</th><th>Stat 4</th><th>Stat 5</th><th>Stat 6</th><th>Stat 7</th><th style="border-right:0">Stat 8</th>
          </tr>
        </thead>
        <tbody>
          <tr><td class="id">Model 1</td><td>Materials</td><td>2019-07-03<br>12:15:00.000</td><td style="padding-left:30px">30.2288</td><td>2.01574</td><td>23.305</td><td>-0.149368</td><td>22.3054</td><td>4.63714</td><td>0.945706</td><td>2.81949</td><td>2.60858</td></tr>
          <tr><td class="id">Model 2</td><td>Industrials</td><td>2019-07-03<br>12:15:00.000</td><td style="padding-left:30px">32.8694</td><td>0.87307</td><td>32.185</td><td>-0.033692</td><td>33.9911</td><td>11.5693</td><td>-0.472968</td><td>-0.830458</td><td>6.80646</td></tr>
          <tr><td class="id">Model 3</td><td>Consumer<br>Discretionary</td><td>2019-07-03<br>12:15:00.000</td><td style="padding-left:30px">1.66002</td><td>-0.569222</td><td>159.814</td><td>0.0252328</td><td>172.616</td><td>10.2875</td><td>-0.750396</td><td>-0.385309</td><td>4.69146</td></tr>
          <tr><td class="id">Model 4</td><td>Information<br>Technology</td><td>2019-07-03<br>12:15:00.000</td><td style="padding-left:30px">45.6856</td><td>0.412148</td><td>202.488</td><td>0.0084923</td><td>205.834</td><td>11.9094</td><td>-0.137913</td><td>0.449595</td><td>3.85106</td></tr>
          <tr><td class="id">Model 5</td><td>Information<br>Technology</td><td>2019-07-03<br>12:15:00.000</td><td style="padding-left:30px">75.7733</td><td>7.06728</td><td>188.605</td><td>0.016913</td><td>161.665</td><td>3.82241</td><td>0.981019</td><td>1.29847</td><td>3.34927</td></tr>
        </tbody>
      </table>
    </main>
  </div>
</div>
</body>
</html>
```